** Wanted ** Wordpress web design for scaffolding rental and construction company

We need a website design and must be functional to show a basic overview of what our company offers as a service. We have a domain name and a logo but we need web design. This web site should have another scaffolding rental page for construction and renovation as well as a quote section where customers can enter their personal information and also upload photos. The site% 26quot; www.brindlework.com% 26quot; should be intuitive, clear and classy ... The logo must be found on the site in several ways.

Target Market(s)

Professional and no professional

Coding

Coded - Design and coding required

Number of Pages Required

3 page

Font styles to use
Serif
Sans Serif
Decorative
Script

Requirements
Must have
• Our logo
Nice to have
• Slogan:% 26quot; The height% 26 # 224; port% 26 # 233; e hand% 26quot;

```html
<!DOCTYPE html>
<html lang="en">
<head>
<meta charset="utf-8">
<title>Brindlework – Scaffolding &amp; Construction</title>
<link rel="stylesheet" href="https://fonts.googleapis.com/css2?family=Roboto:ital,wght@0,400;0,500;0,700;1,400&display=swap">
<style>
:root{
  --blue:#1a87d6;
  --blue-dark:#1b6fb8;
  --ink:#1f1f1f;
  --text:#444;
  --card:#efefef;
  --pale:#e6f2fb;
  --dark:#2b2b2b;
  --white:#fff;
}
*{box-sizing:border-box;margin:0;padding:0}
html,body{width:1200px;height:3265px;overflow:hidden}
body{font-family:"Roboto",sans-serif;color:var(--ink);background:var(--white);position:relative}
.abs{position:absolute}

/* header */
.site-header{position:absolute;left:0;top:0;width:1200px;height:128px;background:var(--white)}
.nav a{position:absolute;top:78px;font-size:15px;color:var(--ink);text-decoration:none}
.nav a.active{color:var(--blue)}
.nav a.active::after{content:"";position:absolute;left:0;right:0;top:49px;height:3px;background:var(--blue)}
.nav a.right{color:var(--blue)}
.brand{position:absolute;left:511px;top:72px;width:178px;height:40px;border:3px solid var(--blue);display:flex;align-items:center;justify-content:center;gap:8px;font-weight:700;font-size:17px;color:var(--blue);letter-spacing:1px}
.brand-dot{width:12px;height:12px;background:var(--blue)}
.top-phone{position:absolute;left:804px;top:16px;display:flex;align-items:center;gap:8px;color:var(--blue);font-size:22px;font-weight:500}
.top-phone .ic{width:28px;height:28px;border-radius:50%;background:var(--blue);display:flex;align-items:center;justify-content:center}

/* hero */
.hero{position:absolute;left:0;top:128px;width:1200px;height:513px;background:linear-gradient(120deg,#6c7d8c 0%,#8fa2b3 35%,#c4a36e 65%,#7a6a52 100%)}
.hero-panel{position:absolute;left:171px;top:90px;width:535px;height:249px;background:rgba(70,70,70,.85);padding:26px 32px;color:var(--white)}
.hero-panel .kicker{font-size:21px;font-weight:500;letter-spacing:.5px}
.hero-panel h1{font-size:35px;font-weight:500;line-height:1.2;margin-top:14px}
.btn-dark{display:inline-block;background:#111;color:var(--white);font-size:11px;font-weight:700;border-radius:16px;text-align:center}
.hero-panel .btn-dark{margin-top:24px;width:138px;height:31px;line-height:31px}
.slider-ctrl{position:absolute;left:571px;top:470px;width:57px;height:43px;background:#111;color:var(--white);font-size:14px;display:flex;align-items:center;justify-content:center;gap:6px}

/* section heading */
.sec-mark{position:absolute;width:14px;height:14px;border-radius:50%;background:var(--blue);left:593px}
.sec-title{position:absolute;left:0;width:1200px;text-align:center;color:var(--blue);font-weight:700}

/* services */
.service{position:absolute;top:741px;height:224px;background:var(--card);padding:18px 21px;overflow:hidden}
.service h3{margin-top:18px;font-size:11.5px;font-weight:700;color:var(--blue);text-transform:uppercase}
.service p{margin-top:10px;font-size:12px;line-height:18px;color:var(--text)}
.corner{position:absolute;right:3px;bottom:3px;width:38px;height:38px}
.pager{position:absolute;top:1020px;left:580px;font-size:16px;color:#333;letter-spacing:20px}

/* welcome */
.welcome{position:absolute;left:0;top:1078px;width:1200px;height:379px;background:var(--blue);color:var(--white);text-align:center}
.welcome .mark{position:absolute;left:593px;top:48px;width:14px;height:14px;border-radius:50%;background:var(--white)}
.welcome h2{position:absolute;top:82px;width:100%;font-size:32px;font-weight:700}
.welcome p{position:absolute;left:230px;width:740px;top:144px;font-size:13.5px;line-height:22.5px}
.welcome .btn-dark{position:absolute;left:531px;top:274px;width:138px;height:33px;line-height:33px}

/* blog */
.blog{position:absolute;left:0;top:1457px;width:1200px;height:426px;background:linear-gradient(180deg,#c9d5df,#dfe7ee 60%,#e8edf1)}
.post-photo{position:absolute;top:133px;width:268px;height:186px}
.post-card{position:absolute;top:288px;width:221px;height:72px;background:var(--white);padding:14px 14px;box-shadow:0 2px 6px rgba(0,0,0,.12)}
.post-card h4{font-size:14px;font-weight:500}
.post-card .date{font-size:10.5px;font-weight:500;margin-top:6px}
.post-card svg{position:absolute;right:16px;bottom:14px}

/* testimonials */
.testimonials{position:absolute;left:0;top:1883px;width:1200px;height:570px;background:var(--pale)}
.quote{position:absolute;top:137px;width:271px;height:230px;background:var(--white);padding:16px 28px}
.quote::after{content:"";position:absolute;left:66px;bottom:-24px;border-left:0 solid transparent;border-right:30px solid transparent;border-top:24px solid var(--white)}
.q-ic{width:34px;height:34px;border-radius:50%;background:var(--blue);color:var(--white);font-weight:700;font-size:22px;text-align:center;line-height:40px}
.quote .when{margin-top:6px;font-size:11px;font-weight:500;color:var(--blue-dark)}
.quote p{margin-top:12px;font-size:11.5px;line-height:18px;font-style:italic;color:var(--text)}
.person{position:absolute;top:394px;display:flex;align-items:center;gap:18px}
.avatar{width:60px;height:60px;border-radius:50%;background:linear-gradient(135deg,#c9a58c,#7a5a48)}
.person .name{font-size:19px;font-weight:500;color:var(--blue)}
.person .role{font-size:10px;color:var(--blue);margin-top:4px}
.dots{position:absolute;top:504px;left:560px;display:flex;gap:16px}
.dots span{width:7px;height:7px;border-radius:50%;background:var(--blue)}
.dots span.on{background:#111}

/* quote form */
.request{position:absolute;left:0;top:2453px;width:1200px;height:531px;background:linear-gradient(160deg,#3a3a3a,#262626 55%,#302c28)}
.field{position:absolute;background:var(--white);font-size:12px;color:#333;padding:0 20px;display:flex;align-items:center;text-transform:uppercase}
.field.area{align-items:flex-start;padding-top:18px}
.btn-blue{position:absolute;left:531px;top:442px;width:138px;height:32px;line-height:32px;border-radius:16px;background:var(--blue);color:var(--white);font-size:11px;font-weight:700;text-align:center}

/* contact band */
.contact-band{position:absolute;left:0;top:2984px;width:1200px;height:149px;background:var(--blue);color:var(--white)}
.cb-item{position:absolute;display:flex;align-items:center;gap:14px}

/* footer */
.footer-nav{position:absolute;top:3163px;left:0;width:1200px;display:flex;justify-content:center;gap:32px;font-size:13px;font-weight:500}
.copyright{position:absolute;top:3198px;width:1200px;text-align:center;font-size:11px;color:#333}
</style>
</head>
<body>

<header class="site-header">
  <nav class="nav">
    <a class="active" style="left:171px">Home</a>
    <a style="left:259px">About Us</a>
    <a style="left:367px">Services</a>
    <a class="right" style="left:785px">Blog</a>
    <a class="right" style="left:862px">Career</a>
    <a class="right" style="left:953px">Contact Us</a>
  </nav>
  <div class="brand"><span class="brand-dot"></span>BRINDLEWORK</div>
  <div class="top-phone">
    <span class="ic"><svg width="14" height="14" viewBox="0 0 24 24"><path fill="#fff" d="M6.6 10.8a15 15 0 0 0 6.6 6.6l2.2-2.2c.3-.3.7-.4 1-.2 1.1.4 2.3.6 3.6.6.6 0 1 .4 1 1V20c0 .6-.4 1-1 1A17 17 0 0 1 3 4c0-.6.4-1 1-1h3.5c.6 0 1 .4 1 1 0 1.3.2 2.5.6 3.6.1.3 0 .7-.2 1z"/></svg></span>
    +1 (800) 555 0142
  </div>
</header>

<section class="hero" role="img" aria-label="Surveyor in hard hat and safety vest on a construction site with cranes at sunset">
  <div class="hero-panel">
    <div class="kicker">BRINDLEWORK</div>
    <h1>Neque porro quisquam est qui dolorem ipsum quia dolor.</h1>
    <span class="btn-dark">LEARN MORE</span>
  </div>
  <div class="slider-ctrl"><span>‹</span><span>›</span></div>
</section>

<!-- services -->
<span class="sec-mark" style="top:666px"></span>
<h2 class="sec-title" style="top:690px;font-size:26px">OUR SERVICES</h2>

<div class="service" style="left:171px;width:274px">
  <svg width="58" height="56" viewBox="0 0 58 56" fill="none" stroke="#1a87d6" stroke-width="2.5"><rect x="4" y="4" width="50" height="48"/><line x1="4" y1="18" x2="54" y2="18"/><line x1="4" y1="38" x2="54" y2="38"/><line x1="4" y1="18" x2="54" y2="38"/><line x1="54" y1="18" x2="4" y2="38"/></svg>
  <h3>Scaffolding Rent</h3>
  <p>Sed ut perspiciatis unde omnis iste natus error sit voluptatem accusantium doloremque laudantium, totam rem aperiam, eaque ipsa</p>
  <svg class="corner" viewBox="0 0 38 38"><path d="M38 0V38H0Z" fill="#1f1f1f"/><path d="M27 20v12M21 26h12" stroke="#fff" stroke-width="2.5"/></svg>
</div>
<div class="service" style="left:464px;width:272px">
  <svg width="58" height="56" viewBox="0 0 58 56" fill="none" stroke="#1a87d6" stroke-width="2.5"><path d="M8 32a21 21 0 0 1 42 0"/><rect x="4" y="32" width="50" height="6"/><path d="M22 14v18M36 14v18"/><path d="M8 44h42v6H36l-3-4h-8l-3 4H8z"/></svg>
  <h3>Construction</h3>
  <p>Sed ut perspiciatis unde omnis iste natus error sit voluptatem accusantium doloremque laudantium, totam rem aperiam, eaque ipsa quae</p>
  <svg class="corner" viewBox="0 0 38 38"><path d="M38 0V38H0Z" fill="#1a87d6"/><path d="M27 20v12M21 26h12" stroke="#fff" stroke-width="2.5"/></svg>
</div>
<div class="service" style="left:754px;width:274px">
  <svg width="58" height="56" viewBox="0 0 58 56" fill="none" stroke="#1a87d6" stroke-width="2.5"><path d="M8 48L40 16M36 6a10 10 0 0 0 14 14l-4-4h-6v-6z"/><path d="M6 8l6-4 10 10-4 4zM22 30l20 20 6-6-20-20"/></svg>
  <h3>Support</h3>
  <p>Sed ut perspiciatis unde omnis iste natus error sit voluptatem accusantium doloremque laudantium, totam rem aperiam, eaque ipsa quae.</p>
  <svg class="corner" viewBox="0 0 38 38"><path d="M38 0V38H0Z" fill="#1f1f1f"/><path d="M27 20v12M21 26h12" stroke="#fff" stroke-width="2.5"/></svg>
</div>
<div class="pager">‹ ›</div>

<section class="welcome">
  <span class="mark"></span>
  <h2>WELCOME TO BRINDLEWORK</h2>
  <p>Lorem ipsum dolor sit amet, consectetur adipiscing elit, sed do eiusmod tempor incididunt ut labore et dolore magna aliqua. Ut enim ad minim veniam, quis nostrud exercitation ullamco laboris nisi ut aliquip ex ea commodo consequat. Duis aute irure dolor in reprehenderit in voluptate velit esse cillum dolore eu fugiat nulla pariatur. Excepteur sint occaecat cupidatat non proident, sunt in culpa qui officia deserunt mollit anim id est laborum.</p>
  <span class="btn-dark">LEARN MORE</span>
</section>

<section class="blog" role="img" aria-label="Faded photo of a builder on scaffolding behind the blog posts">
  <span class="sec-mark" style="top:48px"></span>
  <h2 class="sec-title" style="top:75px;font-size:32px">Blog</h2>

  <div class="post-photo" style="left:174px;background:linear-gradient(135deg,#7a3a2a,#b9c23a 60%,#e0e0e0)" role="img" aria-label="Workers in hi-vis jackets at a scaffold by a window"></div>
  <div class="post-photo" style="left:466px;background:linear-gradient(135deg,#b87a4a,#2a2a2a 55%,#c84a2a)" role="img" aria-label="Worker using a nail gun on roofing"></div>
  <div class="post-photo" style="left:759px;background:linear-gradient(135deg,#4a6a8a,#d9b93a 50%,#9ab0c4)" role="img" aria-label="Worker climbing yellow scaffolding"></div>

  <div class="post-card" style="left:196px"><h4>Featured Content</h4><div class="date">April 22, 2019</div><svg width="16" height="14" viewBox="0 0 16 14"><path d="M1 7h13M8 1l6 6-6 6" stroke="#1b6fb8" stroke-width="2.2" fill="none"/></svg></div>
  <div class="post-card" style="left:489px"><h4>Featured Content</h4><div class="date">April 22, 2019</div><svg width="16" height="14" viewBox="0 0 16 14"><path d="M1 7h13M8 1l6 6-6 6" stroke="#1b6fb8" stroke-width="2.2" fill="none"/></svg></div>
  <div class="post-card" style="left:782px"><h4>Featured Content</h4><div class="date">April 22, 2019</div><svg width="16" height="14" viewBox="0 0 16 14"><path d="M1 7h13M8 1l6 6-6 6" stroke="#1b6fb8" stroke-width="2.2" fill="none"/></svg></div>
</section>

<section class="testimonials">
  <span class="sec-mark" style="top:40px"></span>
  <h2 class="sec-title" style="top:65px;font-size:32px">Testimonials</h2>

  <div class="quote" style="left:171px"><div class="q-ic">”</div><div class="when">19 Hours ago</div><p>Sed ut perspiciatis unde omnis iste natus error sit voluptatem accusantium doloremque laudantium, totam rem aperiam, eaque ipsa quae ab illo inventore veritatis et</p></div>
  <div class="quote" style="left:464px"><div class="q-ic">”</div><div class="when">22 Hours ago</div><p>Sed ut perspiciatis unde omnis iste natus error sit voluptatem accusantium doloremque laudantium, totam rem aperiam, eaque ipsa quae ab illo inventore veritatis et</p></div>
  <div class="quote" style="left:757px"><div class="q-ic">”</div><div class="when">29 Hours ago</div><p>Sed ut perspiciatis unde omnis iste natus error sit voluptatem accusantium doloremque laudantium, totam rem aperiam, eaque ipsa quae ab illo inventore veritatis et</p></div>

  <div class="person" style="left:177px"><div class="avatar" role="img" aria-label="Client portrait"></div><div><div class="name">Nora Pellin</div><div class="role">Founder</div></div></div>
  <div class="person" style="left:469px"><div class="avatar" role="img" aria-label="Client portrait"></div><div><div class="name">Idris Vanhorn</div><div class="role">Founder</div></div></div>
  <div class="person" style="left:762px"><div class="avatar" role="img" aria-label="Client portrait"></div><div><div class="name">Mara Quillet</div><div class="role">Founder</div></div></div>

  <div class="dots"><span></span><span></span><span class="on"></span><span></span></div>
</section>

<section class="request" role="img" aria-label="Darkened photo of builders on a construction site">
  <span class="sec-mark" style="top:46px"></span>
  <h2 class="sec-title" style="top:72px;font-size:32px">Request a Quote</h2>
  <div class="field" style="left:224px;top:152px;width:370px;height:46px">Name</div>
  <div class="field" style="left:606px;top:152px;width:370px;height:46px">Email</div>
  <div class="field" style="left:224px;top:213px;width:370px;height:45px">Phone</div>
  <div class="field" style="left:606px;top:213px;width:370px;height:45px;justify-content:space-between">Upload Photos<svg width="12" height="12" viewBox="0 0 12 12"><path d="M6 1v7M3 4l3-3 3 3M1 10h10" stroke="#333" stroke-width="1.8" fill="none"/></svg></div>
  <div class="field area" style="left:224px;top:274px;width:753px;height:126px">Message</div>
  <span class="btn-blue">SUBMIT</span>
</section>

<section class="contact-band">
  <div class="cb-item" style="left:190px;top:50px;font-size:17px;line-height:21px">
    <svg width="26" height="34" viewBox="0 0 26 34"><path d="M13 0a13 13 0 0 1 13 13c0 9-13 21-13 21S0 22 0 13A13 13 0 0 1 13 0z" fill="#fff"/><circle cx="13" cy="13" r="5" fill="#1a87d6"/></svg>
    <span>#123 Lorium ipsum<br>dolor amit.</span>
  </div>
  <div class="cb-item" style="left:490px;top:50px;font-size:30px;font-weight:500">
    <svg width="28" height="28" viewBox="0 0 24 24"><path fill="#fff" d="M6.6 10.8a15 15 0 0 0 6.6 6.6l2.2-2.2c.3-.3.7-.4 1-.2 1.1.4 2.3.6 3.6.6.6 0 1 .4 1 1V20c0 .6-.4 1-1 1A17 17 0 0 1 3 4c0-.6.4-1 1-1h3.5c.6 0 1 .4 1 1 0 1.3.2 2.5.6 3.6.1.3 0 .7-.2 1z"/></svg>
    <span>1-800 555 0199</span>
  </div>
  <div class="cb-item" style="left:795px;top:58px;font-size:18px;gap:22px">
    <svg width="30" height="22" viewBox="0 0 30 22"><rect x="1" y="1" width="28" height="20" fill="none" stroke="#fff" stroke-width="2.4"/><path d="M1 1l14 11L29 1" fill="none" stroke="#fff" stroke-width="2.4"/></svg>
    <span>hello@brindlework.com</span>
  </div>
</section>

<footer>
  <nav class="footer-nav"><span>Home</span><span>About Us</span><span>Services</span><span>Blog</span><span>Career</span><span>Contact Us</span></nav>
  <div class="copyright">copyright © 2020 &nbsp;|&nbsp; www.brindlework.com</div>
</footer>

</body>
</html>
```